Business Card- Can you make it cool vs boring!

Need a refresh on my business card! Want it to be modern but simple, classic and a pop of coolness! we do senior living and it is boring. but that doesn't mean our business card have to look boring! Open to two sided cards. our website is www.Dunmere-PK.com

Target Market(s)

capital market

Industry/Entity Type

senior housing/ real estate

Contact Information for Business Card

logo/ name/ cell/ address/ www.Dunmere-PK.com/ space for a QR code

Requirements
Must have
• maybe a QR code (do not make prominent I may not use the QR so design where it can be taken out) that link to more about us/ landing page. needs to be modern but clean
Should not have
• clip art or script

```html
<!DOCTYPE html>
<html lang="en">
<head>
<meta charset="utf-8">
<title>Dunmere Living – Business Card</title>
<link rel="stylesheet" href="https://fonts.googleapis.com/css2?family=Poppins:wght@400;500&family=Satisfy&display=swap">
<style>
  :root {
    --backdrop: #a6a2a3;
    --card: #ffffff;
    --rust: #ae4f26;
    --rust-light: #c0602f;
    --rust-dark: #9c4420;
    --ink-grey: #6d6d72;
    --stripe-grey: #8e8e93;
    --white: #ffffff;
  }
  * { box-sizing: border-box; margin: 0; padding: 0; }
  html, body {
    width: 1093px; height: 1200px; overflow: hidden;
    background: var(--backdrop);
    font-family: "Poppins", sans-serif;
  }
  .card {
    position: absolute; left: 264px;
    width: 578px; height: 357px;
    border-radius: 24px; overflow: hidden;
  }
  .card--front { top: 226px; background: var(--card); }
  .card--back  { top: 620px; }

  .accent-bar {
    position: absolute; left: 0; top: 50px;
    width: 17px; height: 49px; background: var(--rust);
  }
  .holder-name {
    position: absolute; left: 26px; top: 42px;
    font-family: "Satisfy", cursive; font-size: 34px;
    color: var(--rust); line-height: 1;
  }
  .holder-title {
    position: absolute; left: 26px; top: 85px;
    font-size: 17px; color: var(--ink-grey); line-height: 1;
  }
  .brand-name {
    position: absolute; right: 29px; top: 60px;
    font-size: 30px; font-weight: 500; letter-spacing: 1px;
    color: var(--rust); line-height: 1;
  }
  .contact-list {
    position: absolute; left: 26px; top: 262px;
    list-style: none; font-size: 17px; line-height: 21px;
    color: var(--ink-grey);
  }
  .contact-list li { display: flex; align-items: center; gap: 7px; }
  .contact-list svg { width: 15px; height: 15px; flex: none; }
  .contact-list .highlight { color: var(--rust); }
  .address {
    position: absolute; right: 29px; top: 283px;
    font-size: 17px; line-height: 21px; text-align: right;
    color: var(--ink-grey); font-style: normal;
  }
  .footer-band {
    position: absolute; left: 0; bottom: 0;
    width: 578px; height: 30px; display: block;
  }

  .back-pattern {
    position: absolute; inset: 0;
    background: linear-gradient(135deg, var(--rust-dark) 0%, var(--rust) 45%, var(--rust-light) 100%);
  }
  .back-brand {
    position: absolute; left: 372px; top: 226px;
    font-size: 20px; font-weight: 500; letter-spacing: 1px;
    color: var(--white); line-height: 1;
  }
</style>
</head>
<body>

<section class="card card--front" aria-label="Card front">
  <div class="accent-bar"></div>
  <h1 class="holder-name">Marcus Hale</h1>
  <p class="holder-title">Managing Director</p>
  <p class="brand-name">Dunmere Living</p>

  <ul class="contact-list">
    <li>
      <svg viewBox="0 0 16 16" aria-hidden="true"><path fill="var(--rust)" d="M3.6 1.2l2.3 2.6-1.3 1.6c.8 1.9 2.2 3.3 4 4.1l1.6-1.3 2.6 2.3-1.2 2.3C6.5 12.6 3.3 9.4 1.3 4.2z"/><path d="M9.5 2.2a4.5 4.5 0 0 1 4.3 4.3M9.5 4.4a2.4 2.4 0 0 1 2.1 2.1" stroke="var(--rust)" stroke-width="1.3" fill="none"/></svg>
      <span>044-123 456 789</span>
    </li>
    <li>
      <svg viewBox="0 0 16 16" aria-hidden="true"><rect x="0.5" y="3" width="15" height="10" fill="var(--rust)"/><path d="M0.5 3l7.5 6 7.5-6M0.5 13l5.5-5M15.5 13l-5.5-5" stroke="var(--white)" stroke-width="1" fill="none"/></svg>
      <span>info@webname.com</span>
    </li>
    <li>
      <svg viewBox="0 0 16 16" aria-hidden="true"><g stroke="var(--rust)" stroke-width="1.4" fill="none"><circle cx="8" cy="8" r="6.8"/><ellipse cx="8" cy="8" rx="3" ry="6.8"/><path d="M1.2 8h13.6M2.2 4.6h11.6M2.2 11.4h11.6"/></g></svg>
      <span>www.<span class="highlight">Dunmere-PK</span>.com</span>
    </li>
  </ul>

  <address class="address">421, Address line goes here<br>45452,Country Name</address>

  <svg class="footer-band" viewBox="0 0 578 30" preserveAspectRatio="none" aria-hidden="true">
    <path fill="var(--rust)" d="M0 17 H276 C284 17 288 7 298 7 H578 V30 H0 Z"/>
    <path fill="var(--stripe-grey)" d="M0 12 H274 L268 19 H0 Z"/>
  </svg>
</section>

<section class="card card--back" aria-label="Card back">
  <div class="back-pattern" role="img" aria-label="Repeating diagonal brand-name pattern in tonal rust shades"></div>
  <p class="back-brand">Dunmere Living</p>
</section>

</body>
</html>
```